New Dental Office Needs an Attractive and user friendly Website Designed

I need a website for a new dental office. The Name is Harrowfield Dentistry. I would like a Modern design with a user friendly interface and usability.
I would like a landing page, a page that lists the services we offer: Cosmetic Dentistry, Implants, Dental Hygiene, Emergency Services, Restorations, Dentures
Target Market(s)
Mid to upper class
Industry/Entity Type
Dentistry
Coding
Number of Pages Required
1 page
Requirements
Must have
- Landing page that has a scheduling option, Procedures, operating hours, and contact us info
Nice to have
- Appealing design, Soft comforting colors. Easy to navigate page, Modern and professional.

```html
<!DOCTYPE html>
<html lang="en">
<head>
<meta charset="utf-8">
<title>Harrowfield Dentistry</title>
<link href="https://fonts.googleapis.com/css2?family=Bree+Serif&family=Lato:wght@400;700;900&display=swap" rel="stylesheet">
<style>
:root{
  --blue:#0a8fd1;
  --blue-dark:#0672b4;
  --band:#c7e8f8;
  --ink:#1e1e1e;
  --muted:#555;
  --grey-band:#d4d6d8;
  --white:#fff;
}
*{box-sizing:border-box;margin:0;padding:0}
html,body{width:1200px;height:4220px;overflow:hidden;background:var(--white)}
body{position:relative;font-family:"Lato",sans-serif;color:var(--ink)}
.abs{position:absolute}
.serif{font-family:"Bree Serif",serif;font-weight:400}
.accent{color:var(--blue)}
.btn{position:absolute;background:var(--blue);color:#fff;font:900 14px "Lato",sans-serif;letter-spacing:.5px;border-radius:22px;display:flex;align-items:center;justify-content:center;text-transform:uppercase}
.brand{font-family:"Lato",sans-serif;font-weight:700;color:var(--ink);line-height:1.05}

/* header */
.topbar{left:400px;top:0;width:800px;height:52px;background:var(--blue);color:#fff;font-size:13px;font-weight:700;display:flex;align-items:center;gap:38px;padding-left:60px}
.topbar span{display:flex;align-items:center;gap:8px}
.topbar svg{width:16px;height:16px}
.nav{left:448px;top:74px;display:flex;gap:36px;font-size:15px}
.nav .active{color:var(--blue);font-weight:700;border-bottom:3px solid var(--blue);padding-bottom:12px}

/* hero */
.hero-photo{left:0;top:113px;width:1200px;height:740px;
  background:
    radial-gradient(ellipse 260px 300px at 440px 300px,rgba(214,170,150,.75),transparent 70%),
    radial-gradient(ellipse 300px 200px at 420px 640px,rgba(170,160,215,.8),transparent 70%),
    radial-gradient(ellipse 140px 120px at 440px 700px,rgba(80,150,225,.8),transparent 70%),
    radial-gradient(ellipse 200px 420px at 60px 500px,rgba(150,120,100,.55),transparent 70%),
    linear-gradient(100deg,#6d7f8c 0%,#b9c0c5 30%,#dfe2e4 65%,#d3d6d8 100%)}
.hero-title{left:600px;top:300px;width:555px;text-align:right;font-size:62px;line-height:84px;color:#fff;text-shadow:0 3px 6px rgba(0,0,0,.35)}
.hero-title .accent{color:var(--blue)}
.dots{display:flex;gap:8px}
.dots i{width:11px;height:11px;border-radius:50%;background:#c9ccd0;display:block}
.dots i.on{background:var(--blue)}

/* about */
h2.sec{font-size:50px;line-height:1}
.about-text{left:110px;top:995px;width:450px;font-size:13px;line-height:30px;color:var(--muted)}
.about-text p+p{margin-top:8px}
.about-circle{left:636px;top:880px;width:450px;height:450px;border-radius:50%;border:3px solid var(--blue);padding:8px}
.about-circle div{width:100%;height:100%;border-radius:50%;
  background:
    radial-gradient(ellipse 90px 80px at 30% 35%,rgba(70,130,225,.85),transparent 70%),
    radial-gradient(ellipse 90px 80px at 75% 55%,rgba(70,130,225,.85),transparent 70%),
    radial-gradient(ellipse 110px 120px at 38% 50%,rgba(222,180,160,.9),transparent 70%),
    radial-gradient(ellipse 160px 120px at 55% 88%,rgba(150,200,230,.9),transparent 70%),
    linear-gradient(160deg,#f3f1ee,#d9dcdf 55%,#a9c8de)}

/* services */
.band{left:0;top:1413px;width:1200px;height:664px;background:var(--band)}
.underline{position:absolute;height:4px;background:var(--blue)}
.svc{top:1559px;width:315px;height:436px;background:#fff;border-radius:0 0 40px 0;overflow:hidden}
.svc .img{width:100%;height:375px;border-radius:0 0 40px 0}
.svc .name{text-align:center;font-size:21px;margin-top:16px}
.svc.featured{border:3px solid var(--blue);border-radius:30px 0 30px 0;padding:10px}
.svc.featured .img{height:240px;border-radius:0 0 40px 0}
.svc.featured .title{text-align:center;color:var(--blue);font-size:20px;margin-top:20px}
.svc.featured p{text-align:center;font-size:12.5px;line-height:24px;color:var(--muted);padding:6px 20px 0}
.arrow{width:32px;height:32px;border-radius:50%;display:flex;align-items:center;justify-content:center}
.arrow.on{background:var(--blue)}
.arrow.off{background:#dfe7ec}

/* journey */
.step{top:2275px;width:306px;height:270px;background:#fff;box-shadow:0 2px 10px rgba(0,0,0,.12);padding:26px 34px 0 34px}
.step.rounded{border-radius:0 0 50px 0}
.step .num{position:absolute;right:28px;top:36px;font:900 64px "Lato",sans-serif;color:#e4e6e8}
.step h3{font-weight:400;font-size:19px;line-height:27px;margin-top:22px}
.step p{font-size:12px;line-height:24px;color:var(--muted);margin-top:8px;text-align:justify}
.step svg{width:62px;height:62px}

/* testimonials */
.tcard{left:113px;top:2643px;width:447px;height:470px;background:#fff;box-shadow:0 2px 12px rgba(0,0,0,.1);text-align:center;padding-top:60px}
.tcard blockquote{font-size:13px;line-height:28px;color:var(--muted);padding:0 50px;margin-top:20px}
.badge{left:622px;top:2761px;width:152px;height:66px;background:#fff;border-radius:4px;box-shadow:0 2px 8px rgba(0,0,0,.2);overflow:hidden}
.badge .bar{position:absolute;left:0;bottom:0;width:100%;height:10px;background:#3b7ddb}
.badge .dot{position:absolute;left:12px;top:14px;width:26px;height:26px;border-radius:50%;border:2px solid #c9ccd0}
.badge .stars{position:absolute;left:48px;top:10px;color:#f2b600;font-size:14px;letter-spacing:2px}
.badge .line{position:absolute;left:48px;top:34px;width:86px;height:5px;border-radius:3px;background:#d8dadc}

/* team */
.member{top:3380px;width:228px;height:270px;background:#fff;border-radius:0 0 26px 26px;box-shadow:0 3px 8px rgba(0,0,0,.15);text-align:center;padding-top:215px}
.member .ph{position:absolute;left:14px;top:-30px;width:200px;height:200px;border-radius:50%;
  background:
    radial-gradient(ellipse 40px 50px at 50% 38%,rgba(205,160,130,.95),transparent 75%),
    radial-gradient(ellipse 90px 60px at 50% 95%,rgba(255,255,255,.95),transparent 75%),
    linear-gradient(180deg,#e6eaee,#c9d3da)}
.member b{display:block;font-size:15px}
.member span{display:block;font-size:15px;margin-top:4px}
.member .soc{position:absolute;left:100px;bottom:-14px;width:28px;height:28px;border-radius:50%;background:var(--blue);border:3px solid #fff}

/* footer */
.footer-bg{left:0;top:3760px;width:1200px;height:460px;background:var(--band)}
.fcol{top:3935px}
.fcol h4{color:var(--blue);font-size:21px;font-weight:400;margin-bottom:14px}
.fcol li{list-style:none;font-size:14.5px;line-height:27.5px}
.contact li{display:flex;align-items:center;gap:14px;line-height:44px}
.social{display:flex;gap:8px}
.social i{width:30px;height:30px;border-radius:50%;background:#fff;border:2px solid var(--blue);display:block;position:relative}
.social i:first-child{background:var(--blue)}
.social i::after{content:"";position:absolute;left:9px;top:9px;width:8px;height:8px;border-radius:50%;background:var(--blue)}
.social i:first-child::after{background:#fff}
</style>
</head>
<body>

<!-- header -->
<div class="abs brand" style="left:105px;top:30px;font-size:28px;width:290px">Harrowfield<br>Dentistry</div>
<div class="abs topbar">
  <span><svg viewBox="0 0 16 16"><circle cx="8" cy="8" r="7" fill="#fff"/><path d="M8 4v4l3 2" stroke="#0a8fd1" stroke-width="1.6" fill="none"/></svg>Opening Hours: Mon - Sat 9am to 10 pm</span>
  <span><svg viewBox="0 0 16 16"><path d="M8 1a5 5 0 0 1 5 5c0 4-5 9-5 9S3 10 3 6a5 5 0 0 1 5-5z" fill="#fff"/><circle cx="8" cy="6" r="2" fill="#0a8fd1"/></svg>Lorem Ipsum,USa -437916</span>
  <span><svg viewBox="0 0 16 16"><path d="M3 1l3 3-1.5 2a9 9 0 0 0 5 5L11 9.5l3 3-2 2C6 14 2 10 1 3z" fill="#fff"/></svg>01400 522 617</span>
</div>
<nav class="abs nav"><span class="active">Home</span><span>About Us</span><span>Services</span><span>Blog</span><span>Testimonials</span></nav>
<div class="btn" style="left:954px;top:66px;width:136px;height:38px">Contact Us</div>

<!-- hero -->
<div class="abs hero-photo" role="img" aria-label="Smiling patient in a dental chair with a dentist beside her"></div>
<svg class="abs" style="left:0;top:700px" width="1200" height="160" viewBox="0 0 1200 160">
  <path d="M0 110 Q500 190 1200 95 L1200 160 L0 160Z" fill="#fff"/>
  <path d="M30 125 Q350 175 700 120 Q900 90 1060 65 Q900 80 700 108 Q380 160 30 118Z" fill="#0a8fd1"/>
  <path d="M1050 75 Q1150 100 1200 145 L1200 160 Q1130 110 1050 75Z" fill="#fff"/>
</svg>
<h1 class="abs serif hero-title">Modern Care for<br><span class="accent">Brighter Smiles</span></h1>
<div class="btn" style="left:884px;top:483px;width:264px;height:42px">Schedule an Appointment</div>
<div class="abs dots" style="left:575px;top:680px"><i></i><i class="on"></i><i></i><i></i></div>

<!-- about -->
<h2 class="abs serif sec" style="left:110px;top:915px">About <span class="accent">Us</span></h2>
<div class="abs" style="left:110px;top:980px;width:70px;height:3px;background:var(--blue)"></div>
<div class="abs about-text">
  <p>At Harrowfield Dentistry, we believe that a healthy smile is the foundation of a happy life. Our mission is to provide exceptional dental care in a comfortable, modern environment where patients of all ages feel welcome and at ease.</p>
  <p>We combine advanced technology with a compassionate, personalized approach to ensure every visit is as stress-free and effective as possible. From routine cleanings to complex procedures, our experienced team is here to support your oral health every step of the way.</p>
</div>
<div class="btn" style="left:112px;top:1268px;width:135px;height:42px">Read More</div>
<div class="abs about-circle"><div role="img" aria-label="Dentist examining a smiling patient"></div></div>

<!-- services -->
<div class="abs band"></div>
<h2 class="abs serif" style="left:0;top:1452px;width:1200px;text-align:center;font-size:44px">Services <span class="accent">We Offer</span></h2>
<div class="underline" style="left:528px;top:1510px;width:145px"></div>
<div class="abs arrow on" style="left:34px;top:1754px"><svg width="12" height="12" viewBox="0 0 12 12"><path d="M8 1L3 6l5 5" stroke="#fff" stroke-width="2" fill="none"/></svg></div>
<div class="abs arrow off" style="left:1122px;top:1754px"><svg width="12" height="12" viewBox="0 0 12 12"><path d="M4 1l5 5-5 5" stroke="#fff" stroke-width="2" fill="none"/></svg></div>
<div class="abs svc" style="left:112px">
  <div class="img" role="img" aria-label="Teeth whitening with a blue light" style="background:radial-gradient(ellipse 110px 90px at 60% 42%,rgba(220,225,255,.95),transparent 75%),radial-gradient(ellipse 160px 140px at 55% 45%,rgba(90,95,235,.95),transparent 75%),linear-gradient(160deg,#141631,#2d2f72 45%,#8f95c8 85%,#c8ccde)"></div>
  <div class="name">Cosmetic Dentistry</div>
</div>
<div class="abs svc featured" style="left:443px">
  <div class="img" role="img" aria-label="Dental implant model" style="background:radial-gradient(ellipse 90px 70px at 55% 40%,rgba(235,150,165,.9),transparent 75%),radial-gradient(ellipse 90px 50px at 30% 55%,rgba(40,120,100,.6),transparent 75%),linear-gradient(160deg,#f6f6f6,#eaeaea 60%,#dcdedf)"></div>
  <svg class="abs" style="left:137px;top:222px" width="40" height="40" viewBox="0 0 40 40"><circle cx="20" cy="20" r="19" fill="#fff"/><path d="M13 11h14v4l-2 2v3h-10v-3l-2-2z" fill="#0a8fd1"/><path d="M16 22h8M16 25h8M17 28h6M18 31h4" stroke="#0a8fd1" stroke-width="2"/></svg>
  <div class="title">Implants</div>
  <p>Lorem ipsum dolor sit amet, consectetur adipiscing elit, sed do eiusmod tempor incididunt ut labore et dolore magna aliqua.</p>
</div>
<div class="abs svc" style="left:776px">
  <div class="img" role="img" aria-label="Denture model with dental tool" style="background:radial-gradient(ellipse 130px 60px at 60% 45%,rgba(240,228,205,.98),transparent 75%),linear-gradient(180deg,#f1f2f4 0%,#e6e8eb 40%,#7c9ade 62%,#5573cf 100%)"></div>
  <div class="name">Dentures</div>
</div>

<!-- journey -->
<h2 class="abs serif" style="left:0;top:2162px;width:1200px;text-align:center;font-size:42px">Start Your <span class="accent">Perfect Smile Journey</span></h2>
<div class="underline" style="left:545px;top:2213px;width:128px"></div>

<div class="abs" style="left:107px;top:2485px;width:313px;height:65px;border:6px solid var(--blue);border-top:none"></div>
<div class="abs step rounded" style="left:113px">
  <div class="num">1</div>
  <svg viewBox="0 0 62 62" fill="none" stroke="#0a8fd1" stroke-width="2"><rect x="4" y="6" width="38" height="30" rx="4"/><rect x="22" y="24" width="34" height="28" rx="4"/><circle cx="40" cy="38" r="6"/><path d="M12 16c4 5 14 5 18 0"/></svg>
  <h3>Send us your smile selfies</h3>
  <p>Lorem ipsum dolor sit amet, consectetur adipiscing elit, sed do eiusmod tempor incididunt ullamco laboris nisi ut.</p>
</div>
<div class="abs" style="left:438px;top:2268px;width:312px;height:60px;border:6px solid var(--blue);border-bottom:none"></div>
<div class="abs step rounded" style="left:444px">
  <div class="num">2</div>
  <svg viewBox="0 0 62 62" fill="none" stroke="#0a8fd1" stroke-width="2"><rect x="22" y="10" width="34" height="24"/><path d="M22 10l17 14 17-14"/><path d="M6 30l6-4 5 7-3 3c2 5 6 9 11 11l3-3 7 5-4 6C16 54 6 42 6 30z"/></svg>
  <h3>Tell us what you're hoping to achieve</h3>
  <p>Lorem ipsum dolor sit amet, consectetur adipiscing elit, sed do eiusmod tempor incididunt ullamco laboris nisi ut.</p>
</div>
<div class="abs" style="left:771px;top:2485px;width:313px;height:65px;border:6px solid var(--blue);border-top:none"></div>
<div class="abs step" style="left:777px">
  <div class="num">2</div>
  <svg viewBox="0 0 62 62" fill="none" stroke="#0a8fd1" stroke-width="2"><circle cx="31" cy="16" r="8"/><path d="M28 24v4h6v-4M31 2v4M19 8l3 3M43 8l-3 3"/><circle cx="14" cy="36" r="5"/><circle cx="48" cy="36" r="5"/><path d="M4 56c0-8 5-12 10-12s10 4 10 12M38 56c0-8 5-12 10-12s10 4 10 12M20 48h22"/></svg>
  <h3>Discuss your smile plan with us today</h3>
  <p>Lorem ipsum dolor sit amet, consectetur adipiscing elit, sed do eiusmod tempor incididunt ullamco laboris nisi ut.</p>
</div>

<!-- testimonials -->
<div class="abs" style="left:0;top:2675px;width:1200px;height:400px;background:var(--grey-band)"></div>
<div class="abs" style="left:560px;top:2643px;width:24px;height:32px;background:var(--blue);clip-path:polygon(0 0,50% 0,100% 100%,0 100%)"></div>
<div class="abs" role="img" aria-label="Smiling woman giving two thumbs up" style="left:584px;top:2675px;width:616px;height:400px;background:radial-gradient(ellipse 70px 90px at 64% 30%,rgba(215,170,145,.95),transparent 75%),radial-gradient(ellipse 150px 130px at 64% 80%,rgba(250,250,250,.95),transparent 75%),radial-gradient(ellipse 90px 150px at 64% 35%,rgba(110,75,55,.7),transparent 75%),linear-gradient(90deg,#cdcfd1,#d9dadb 60%,#c9cbcd)"></div>
<div class="abs badge"><i class="dot"></i><span class="stars">★★★★★</span><i class="line"></i><i class="bar"></i></div>
<div class="abs tcard">
  <h2 class="serif" style="font-size:42px">Client <span class="accent">Testimonials</span></h2>
  <div style="width:80px;height:3px;background:var(--blue);margin:4px auto 0 220px"></div>
  <div style="margin-top:18px;font-size:18px;color:#f2b600;letter-spacing:2px"><span style="display:inline-block;width:16px;height:16px;border-radius:50%;background:var(--blue);vertical-align:-2px;margin-right:8px"></span>★★★★★</div>
  <div style="color:var(--blue);font-size:20px;margin-top:20px">A Truly Wonderful Experience!</div>
  <blockquote>“The team at Harrowfield Dentistry made me feel comfortable from the moment I walked in. The space is beautiful and calming, and the care I received was top-notch. I actually look forward to my appointments now!”</blockquote>
  <div style="margin-top:24px;font-size:16px">Jenna.R</div>
  <div class="dots" style="justify-content:center;margin-top:12px"><i></i><i class="on"></i><i></i><i></i></div>
</div>

<!-- team -->
<h2 class="abs serif" style="left:0;top:3180px;width:1200px;text-align:center;font-size:44px">Our <span class="accent">Team</span></h2>
<div class="underline" style="left:588px;top:3232px;width:85px"></div>
<p class="abs" style="left:210px;top:3258px;width:780px;text-align:center;font-size:13px;line-height:25px;color:var(--muted)">At Harrowfield Dentistry, our team is the heart of everything we do. We're passionate about creating a comfortable, friendly experience for every patient — backed by years of professional training and a commitment to your care.</p>
<div class="abs arrow on" style="left:36px;top:3476px"><svg width="12" height="12" viewBox="0 0 12 12"><path d="M8 1L3 6l5 5" stroke="#fff" stroke-width="2" fill="none"/></svg></div>
<div class="abs arrow off" style="left:1124px;top:3476px"><svg width="12" height="12" viewBox="0 0 12 12"><path d="M4 1l5 5-5 5" stroke="#fff" stroke-width="2" fill="none"/></svg></div>
<div class="abs member" style="left:115px"><div class="ph" role="img" aria-label="Portrait of lead dentist"></div><b>Dr. Elena Marsh, DDS</b><span>Lead Dentist &amp; Founder</span><i class="soc"></i></div>
<div class="abs member" style="left:364px"><div class="ph" role="img" aria-label="Portrait of dental hygienist"></div><b>Clara Benton</b><span>Dental Hygienist</span><i class="soc"></i></div>
<div class="abs member" style="left:613px"><div class="ph" role="img" aria-label="Portrait of dental assistant"></div><b>Owen Reyes</b><span>Dental Assistant</span><i class="soc"></i></div>
<div class="abs member" style="left:862px"><div class="ph" role="img" aria-label="Portrait of expanded function dental assistant"></div><b>Talia Quinn</b><span>EFDA</span><i class="soc"></i></div>

<!-- footer -->
<div class="abs footer-bg"></div>
<svg class="abs" style="left:0;top:3700px" width="1200" height="180" viewBox="0 0 1200 180">
  <path d="M0 90 Q200 40 420 70 Q700 120 1200 60 L1200 0 L0 0Z" fill="#fff"/>
  <path d="M40 60 Q220 20 420 55 Q700 110 1070 95 Q700 130 420 70 Q220 35 40 60Z" fill="#0a8fd1"/>
</svg>
<div class="abs brand" style="left:108px;top:3935px;font-size:34px;width:320px">Harrowfield<br>Dentistry</div>
<div class="abs social" style="left:112px;top:4060px"><i></i><i></i><i></i><i></i></div>
<div class="btn" style="left:110px;top:4120px;width:135px;height:42px">Contact Us</div>
<div class="abs fcol" style="left:485px"><h4>Quick Links</h4><ul><li>Home</li><li>About Us</li><li>Services</li><li>Blog</li><li>Testimonials</li><li>Contact Us</li></ul></div>
<div class="abs fcol" style="left:674px"><h4>Help Links</h4><ul><li>Privacy Policy</li><li>Terms of Use</li><li>Trading Terms</li><li>Terms of Service</li><li>Complaints Policy</li><li>Guarantee Policy</li></ul></div>
<div class="abs fcol contact" style="left:843px"><h4 style="margin-bottom:0">Contac Info</h4><ul>
  <li><svg width="16" height="18" viewBox="0 0 16 18"><path d="M8 1a6 6 0 0 1 6 6c0 5-6 10-6 10S2 12 2 7a6 6 0 0 1 6-6z" fill="#0a8fd1"/><circle cx="8" cy="7" r="2" fill="#fff"/></svg>Lorem ipsum,USA -437916</li>
  <li><svg width="16" height="16" viewBox="0 0 16 16"><path d="M3 1l3 3-1.5 2a9 9 0 0 0 5 5L11 9.5l3 3-2 2C6 14 2 10 1 3z" fill="#0a8fd1"/></svg>888 888 8888</li>
  <li><svg width="16" height="12" viewBox="0 0 16 12"><rect width="16" height="12" fill="#0a8fd1"/><path d="M0 0l8 6 8-6" stroke="#fff" fill="none"/></svg>info@harrowfielddentistry.com</li>
  <li><svg width="16" height="16" viewBox="0 0 16 16"><circle cx="8" cy="8" r="7.5" fill="#0a8fd1"/><path d="M8 4v4l3 2" stroke="#fff" stroke-width="1.6" fill="none"/></svg>Mon- Sat : 9.am &nbsp;to 10.pm</li>
</ul></div>
<div class="abs" style="left:110px;top:4170px;width:980px;height:1px;background:#8fb8cf"></div>
<div class="abs" style="left:0;top:4183px;width:1200px;text-align:center;font-size:13px">© 2025 &nbsp;Harrowfield Dentistry All rights reserved.</div>

</body>
</html>
```